Corvex Hiring Partners Business Cards

Business cards with logo design for a new recruiting company called "Corvex Hiring Partners"

incorporate RED & BLUE colors

Final design should reflect strength - clean, elegant design

Company name superimposed upon graphic (Greek Columns)

Please see attached Photos!!!

Industry/Entity Type

Business

Font styles to use
Decorative

Colors
ec2027
0555a3
85cae6

Requirements
Must have
• Must look very similar to attached design!!!

Want Company name superimposed upon graphic (Greek Columns)

Tag line at bottom must be included:
"Connecting Ambitious Companies with Remarkable Talent"

```html
<!DOCTYPE html>
<html lang="en">
<head>
<meta charset="utf-8">
<title>Corvex Hiring Partners – Business Card</title>
<link rel="stylesheet" href="https://fonts.googleapis.com/css2?family=Lato:wght@400;700;900&display=swap">
<style>
  :root {
    --brand-red: #ec2027;
    --brand-blue: #0555a3;
    --brand-sky: #85cae6;
    --ink: #1a1a1a;
    --paper: #ffffff;
    --backdrop: #6a6a6a;
    --rule: #111111;
  }
  * { margin: 0; padding: 0; box-sizing: border-box; }
  html, body {
    width: 1200px;
    height: 900px;
    overflow: hidden;
    background: var(--backdrop);
    font-family: "Lato", sans-serif;
  }
  .stage {
    width: 1200px;
    height: 900px;
    display: flex;
    align-items: center;
    justify-content: center;
  }
  .business-card {
    position: relative;
    width: 1000px;
    height: 572px;
    background: var(--paper);
    overflow: hidden;
  }
  .brand-block {
    position: absolute;
    left: 60px;
    top: 120px;
    width: 340px;
    display: flex;
    align-items: flex-start;
    gap: 20px;
  }
  .brand-square {
    flex: none;
    width: 34px;
    height: 34px;
    margin-top: 12px;
    background: var(--brand-red);
  }
  .brand-name {
    color: var(--brand-blue);
    font-weight: 900;
    font-size: 54px;
    line-height: 1.1;
    letter-spacing: 0.5px;
  }
  .contact-block {
    position: absolute;
    left: 470px;
    top: 195px;
  }
  .person-name {
    color: var(--brand-blue);
    font-weight: 400;
    font-size: 40px;
    line-height: 1.1;
    margin-bottom: 26px;
  }
  .contact-list {
    list-style: none;
    font-size: 25px;
    line-height: 1.42;
    color: var(--ink);
  }
  .contact-label {
    color: var(--brand-red);
    margin-right: 8px;
  }
  .divider-rule {
    position: absolute;
    left: 0;
    right: 0;
    top: 448px;
    height: 5px;
    background: var(--rule);
  }
  .tagline-band {
    position: absolute;
    left: 0;
    right: 0;
    bottom: 0;
    height: 112px;
    background: var(--brand-red);
    display: flex;
    align-items: center;
    justify-content: center;
  }
  .tagline {
    color: var(--paper);
    font-weight: 700;
    font-size: 30px;
    letter-spacing: 0.3px;
    white-space: nowrap;
  }
</style>
</head>
<body>
  <main class="stage">
    <article class="business-card">
      <div class="brand-block">
        <span class="brand-square" aria-hidden="true"></span>
        <p class="brand-name">Corvex<br>Hiring<br>Partners</p>
      </div>

      <section class="contact-block">
        <h1 class="person-name">Daniel R Whitmore</h1>
        <ul class="contact-list">
          <li><span class="contact-label">p.</span>512 555 014</li>
          <li><span class="contact-label">w.</span>CorvexHP.com</li>
          <li><span class="contact-label">e.</span>DWhitmore@CorvexHP.com</li>
        </ul>
      </section>

      <div class="divider-rule" aria-hidden="true"></div>
      <footer class="tagline-band">
        <p class="tagline">Connecting Ambitious Companies with Remarkable Talent</p>
      </footer>
    </article>
  </main>
</body>
</html>
```